BLS Business Card 2018

Larkmere Chiropractic. We have two locations that we want to advertise on the same card. Brightvale OrthoCore campus address: 3815 Pellham Dr., Suite 240, Flowood, MS 39417. Madison address: 246 Willowmere Dr., Building D., Madison, MS 39284. website: www.drlarkmere-example.com. o:(601)555-0147 f:(601)555-0183

Target Market(s)

Health care decision makers: primary care doctors and mothers

Contact Information for Business Card

I have no idea; up for any suggestions and I'd do much better picking from examples versus describing what I'm looking for. We are in a very high end location and would like the cards to look really sharp.

Requirements
Must have
• My name, Martin R Belvane, D.C.

```html
<!DOCTYPE html>
<html lang="en">
<head>
<meta charset="utf-8">
<title>Larkmere Chiropractic Business Card</title>
<link rel="stylesheet" href="https://fonts.googleapis.com/css2?family=Merriweather:wght@400;700&display=swap">
<style>
  :root {
    --stage: #3b3b3d;
    --card: #262628;
    --card-deep: #1f1f21;
    --band: #0c5e86;
    --accent: #1a86d0;
    --ink: #ffffff;
    --muted: #cfd3d7;
    --emboss: #3a3a3d;
  }
  * { margin: 0; padding: 0; box-sizing: border-box; }
  html, body { width: 799px; height: 1200px; overflow: hidden; }
  body {
    background: var(--stage);
    font-family: "Merriweather", Georgia, serif;
    color: var(--ink);
    position: relative;
  }
  .card {
    position: absolute;
    left: 60px;
    width: 680px;
    height: 390px;
    border-radius: 26px;
    background: var(--card);
    overflow: hidden;
  }
  .card--front { top: 150px; }
  .card--back { top: 680px; }

  /* front */
  .front-brand {
    position: absolute;
    top: 52px; right: 46px;
    text-align: right;
    color: var(--emboss);
    font-weight: 700;
    font-size: 44px;
    line-height: 1.05;
    text-transform: uppercase;
    letter-spacing: 1px;
  }
  .front-brand .brand-mark {
    display: inline-block;
    width: 14px; height: 14px;
    border-radius: 50%;
    background: var(--emboss);
    margin-right: 12px;
    vertical-align: middle;
  }
  .band {
    position: absolute;
    left: 0; right: 0;
    top: 178px; height: 100px;
    background: var(--band);
  }
  .campus-pill {
    position: absolute;
    top: 158px; left: 50%;
    transform: translateX(-50%);
    background: var(--card-deep);
    border: 2px solid var(--ink);
    border-radius: 20px;
    padding: 9px 30px;
    font-size: 15px;
    font-weight: 700;
    white-space: nowrap;
    z-index: 2;
  }
  .address {
    position: absolute;
    top: 206px;
    font-size: 15px;
    line-height: 1.4;
    display: flex;
    gap: 10px;
  }
  .address--left { left: 38px; }
  .address--right { left: 360px; }
  .address .pin { width: 13px; height: 17px; flex: none; margin-top: 2px; }
  .band-divider {
    position: absolute;
    left: 338px; top: 212px;
    width: 1px; height: 46px;
    background: rgba(255,255,255,0.35);
  }
  .front-web {
    position: absolute;
    top: 310px; left: 0; right: 0;
    display: flex; align-items: center; justify-content: center;
    gap: 22px;
    font-size: 17px;
  }
  .front-web .rule { width: 60px; height: 2px; background: var(--ink); }

  /* back */
  .figure-art {
    position: absolute;
    left: 0; top: 0;
    width: 330px; height: 390px;
    background: linear-gradient(135deg, #1c5f95 0%, #174a74 45%, #262628 100%);
  }
  .back-brand {
    position: absolute;
    top: 58px; right: 40px;
    text-align: right;
    font-size: 40px;
    line-height: 1.05;
    font-weight: 700;
    text-transform: uppercase;
    letter-spacing: 1px;
    color: var(--ink);
  }
  .person {
    position: absolute;
    top: 172px; right: 40px;
    text-align: right;
  }
  .person-name {
    color: var(--accent);
    font-size: 24px;
    font-weight: 400;
  }
  .person-role {
    font-size: 13px;
    margin-top: 4px;
    color: var(--muted);
  }
  .contact-list {
    position: absolute;
    top: 262px; right: 40px;
    list-style: none;
    text-align: right;
    font-size: 15px;
    line-height: 1.5;
  }
  .contact-list li { display: flex; justify-content: flex-end; align-items: center; gap: 10px; }
  .contact-list svg { width: 14px; height: 14px; flex: none; }
</style>
</head>
<body>

<section class="card card--front" aria-label="Card front">
  <div class="front-brand"><span class="brand-mark"></span>Larkmere<br>Chiropractic</div>
  <div class="band"></div>
  <div class="campus-pill">OrthoCore Campus</div>

  <div class="address address--left">
    <svg class="pin" viewBox="0 0 13 17"><path d="M6.5 0A6.5 6.5 0 0 0 0 6.5C0 11 6.5 17 6.5 17S13 11 13 6.5A6.5 6.5 0 0 0 6.5 0Zm0 9A2.5 2.5 0 1 1 6.5 4a2.5 2.5 0 0 1 0 5Z" fill="#fff"/></svg>
    <p>3815 Pellham Dr., Suite 240,<br>Flowood, MS 39417</p>
  </div>
  <div class="band-divider"></div>
  <div class="address address--right">
    <svg class="pin" viewBox="0 0 13 17"><path d="M6.5 0A6.5 6.5 0 0 0 0 6.5C0 11 6.5 17 6.5 17S13 11 13 6.5A6.5 6.5 0 0 0 6.5 0Zm0 9A2.5 2.5 0 1 1 6.5 4a2.5 2.5 0 0 1 0 5Z" fill="#fff"/></svg>
    <p>246 Willowmere Dr., Building D.,<br>Madison, MS 39284</p>
  </div>

  <div class="front-web"><span class="rule"></span>www.drlarkmere-example.com<span class="rule"></span></div>
</section>

<section class="card card--back" aria-label="Card back">
  <div class="figure-art" role="img" aria-label="Blue line illustration of a human back and shoulders"></div>
  <div class="back-brand">Larkmere<br>Chiropractic</div>
  <div class="person">
    <p class="person-name">Martin R Belvane, D.C.</p>
    <p class="person-role">Managing Director</p>
  </div>
  <ul class="contact-list">
    <li>(601)555-0147
      <svg viewBox="0 0 14 14"><path d="M3 1l2 3-1.3 1.3a8 8 0 0 0 5 5L10 9l3 2-1 2.5C6 13.5.5 8 .5 2Z" fill="#1a86d0"/></svg></li>
    <li>(601)555-0183
      <svg viewBox="0 0 14 14"><rect x="3" y="1" width="8" height="4" fill="#1a86d0"/><rect x="1" y="5" width="12" height="6" rx="1" fill="#1a86d0"/><rect x="3" y="9" width="8" height="4" fill="#fff"/></svg></li>
    <li>m.r.belvane@drlarkmere-example.com
      <svg viewBox="0 0 14 14"><rect x="1" y="3" width="12" height="8" fill="#1a86d0"/><path d="M1 3l6 5 6-5" stroke="#fff" fill="none"/></svg></li>
    <li>www.drlarkmere-example.com
      <svg viewBox="0 0 14 14"><circle cx="7" cy="7" r="6" fill="#1a86d0"/><path d="M1 7h12M7 1c-3 3-3 9 0 12M7 1c3 3 3 9 0 12" stroke="#fff" fill="none" stroke-width="0.8"/></svg></li>
  </ul>
</section>

</body>
</html>
```